Refresh existing website - vrtmdp.org

Apply these upgrades to the existing website
1. Modern Design: Update the overall aesthetic to a clean, contemporary look with bold typography,
vibrant colors, and improved visual hierarchy.
2. Mobile Optimization: Enhance responsiveness for seamless navigation on mobile devices.
3. Intuitive User Interface: Simplify navigation by reducing menu complexity and improving call-to-
action buttons.
4. SEO Optimization: Improve content for better ranking on search engines.
5. Accessibility: Ensure compliance with WCAG standards for inclusivity.
6. Faster Load Times: Optimize images and scripts for better performance.
7. Social Media Integration: Add live social media feeds to showcase community engagement.
8. Prefer html

```html
<!DOCTYPE html>
<html lang="en">
<head>
<meta charset="utf-8">
<title>NGCHPA – Healthcare Practice Advisors</title>
<link rel="stylesheet" href="https://fonts.googleapis.com/css2?family=Lato:wght@400;700;900&display=swap">
<style>
:root{
  --green:#6a8b2a;
  --green-dark:#5a7822;
  --slate:#3f5568;
  --slate-dark:#34485a;
  --ink:#2f3a45;
  --text:#4a4f55;
  --muted:#f0f0f0;
  --white:#ffffff;
}
*{box-sizing:border-box;margin:0;padding:0}
html,body{width:1200px;height:4464px;overflow:hidden;background:var(--white)}
body{font-family:'Lato',sans-serif;color:var(--text);position:relative}
.abs{position:absolute}
a{color:inherit;text-decoration:none}

/* header */
.topbar{position:absolute;left:425px;top:0;width:775px;height:48px;background:var(--green);clip-path:polygon(0 0,100% 0,100% 100%,26px 100%)}
.topbar ul{list-style:none;display:flex;gap:22px;position:absolute;right:112px;top:16px;font-size:12px;color:var(--white)}
.topbar li::before{content:"";display:inline-block;width:10px;height:10px;border-radius:2px;background:rgba(255,255,255,.8);margin-right:6px;vertical-align:-1px}
.brand{left:111px;top:20px;width:236px;height:72px;display:flex;align-items:center;gap:10px}
.brand-mark{width:18px;height:18px;background:var(--green)}
.brand-name{font-size:46px;font-weight:700;color:var(--slate);letter-spacing:1px}
.nav{left:434px;top:58px;display:flex;gap:0;font-size:15px;color:var(--ink)}
.nav a{display:flex;align-items:center;justify-content:center;text-align:center;line-height:1.1;height:42px;padding:0 18px}
.nav a.active{background:var(--slate);color:var(--white);font-weight:700;padding:0 14px}

/* hero */
.hero{left:0;top:111px;width:1200px;height:600px;background:linear-gradient(120deg,#6d7781 0%,#9ea6ad 40%,#8c949a 60%,#4b5258 100%)}
.hero-shade{left:0;top:111px;width:1200px;height:600px;background:rgba(30,40,50,.35)}
.hero-title{left:0;top:320px;width:1200px;text-align:center;font-size:82px;font-weight:700;color:var(--white)}
.hero-sub{left:0;top:413px;width:1200px;text-align:center;font-size:34px;font-weight:700;color:var(--white)}
.btn{display:inline-flex;align-items:center;justify-content:center;background:var(--green);color:var(--white);font-weight:700;font-size:15px;border-radius:2px}
.hero .btn,.hero-btn{left:538px;top:473px;width:123px;height:42px}
.dots{left:576px;top:653px;display:flex;gap:4px}
.dots i{width:14px;height:4px;background:var(--white);display:block}

/* section titles */
.sec-title{font-size:44px;font-weight:700;color:var(--slate);letter-spacing:-.5px}
.sec-title em{font-style:normal;color:var(--green)}
.center{left:0;width:1200px;text-align:center}
.rule{height:4px;width:50px;background:var(--slate)}

/* about */
.about-frame{left:140px;top:884px;width:420px;height:427px;border:10px solid var(--green);border-left:none;border-top:none}
.photo{background:linear-gradient(160deg,#d8dde0,#aab3b8 55%,#6f7c86)}
.about-photo{left:111px;top:798px;width:434px;height:496px;border:4px solid var(--white)}
.tabs{background:var(--muted);display:flex;align-items:center;font-size:16px;color:var(--text)}
.tabs span{padding:0 16px}
.tabs .on{color:var(--green);font-weight:700;position:relative}
.tabs .on::after{content:"";position:absolute;left:16px;right:16px;bottom:-14px;height:3px;background:var(--green)}
.sub-head{font-size:21px;color:var(--slate);font-weight:700}
.body-copy{font-size:14.5px;line-height:22px;color:var(--text)}
.btn-sm{height:42px;width:124px}

/* cards */
.card-img{width:310px;height:214px;border-radius:2px}
.card-title{width:310px;font-size:20px;font-weight:700;color:var(--slate);line-height:26px}
.card-text{width:300px;font-size:14px;line-height:22px}
.more{font-size:14px;font-weight:700;color:var(--green)}
.arrow{width:32px;height:32px}

/* foundation */
.band{left:0;top:1991px;width:1200px;height:477px;background:linear-gradient(180deg,#6e8f2c,#5f7f24)}
.band-title{top:2066px;font-size:43px;font-weight:700;color:var(--white);line-height:52px}
.band-text{left:150px;top:2212px;width:900px;text-align:center;font-size:15.5px;line-height:23.5px;color:var(--white)}
.btn-slate{background:var(--slate)}

/* partners */
.badge{height:98px;background:var(--white);box-shadow:0 0 0 1px #e4e4e4,0 3px 6px rgba(0,0,0,.12);display:flex;align-items:center;justify-content:center}
.badge i{display:block;background:#c9ced3;border-radius:4px}

/* education */
.edu-title{width:310px;text-align:center;font-size:20px;color:var(--slate);font-weight:700}

/* membership */
.mem-frame{left:635px;top:3468px;width:370px;height:425px;border-left:10px solid var(--slate);border-bottom:10px solid var(--slate)}
.mem-photo{left:650px;top:3383px;width:434px;height:496px;background:linear-gradient(150deg,#3d3a36,#7a6a5a 45%,#d6cdb8 60%,#3a3631);border:4px solid var(--white)}
.bullets{list-style:none;font-size:14.5px;line-height:20px}
.bullets li{position:relative;padding-left:22px;margin-bottom:12px}
.bullets li::before{content:"";position:absolute;left:0;top:7px;width:8px;height:8px;border-radius:50%;background:var(--slate)}

/* footer */
.footer{left:0;top:3983px;width:1200px;height:481px;background:var(--slate)}
.foot-head{font-size:21px;font-weight:700;color:var(--white)}
.foot-links{list-style:none;font-size:14px;color:var(--white)}
.foot-links li{height:43px}
.contact{font-size:14px;line-height:22px;color:var(--white)}
.social{display:flex;gap:14px;font-size:12px;color:var(--white);align-items:center}
.social span{display:flex;align-items:center;gap:4px}
.social span::before{content:"";width:10px;height:10px;border-radius:50%;background:var(--white)}
.foot-rule{left:111px;top:4418px;width:978px;height:1px;background:rgba(255,255,255,.35)}
.legal{top:4436px;font-size:12px;color:var(--white)}
</style>
</head>
<body>

<header>
  <div class="topbar">
    <ul>
      <li>Get Certified(CHPA)</li><li>Find A Consultant</li><li>Current News</li><li>Current Podcasts</li><li>Member Login</li>
    </ul>
  </div>
  <a class="abs brand" href="#"><span class="brand-mark"></span><span class="brand-name">NGCHPA</span></a>
  <nav class="abs nav">
    <a class="active" href="#">Home</a>
    <a href="#">About the<br>Society</a>
    <a href="#">About<br>Membership</a>
    <a href="#">Products/<br>Services</a>
    <a href="#">Upcoming<br>Education</a>
    <a href="#">Practice<br>Reports</a>
    <a href="#">More ⌄</a>
  </nav>
</header>

<section aria-label="Hero">
  <div class="abs hero" role="img" aria-label="Smiling consultant meeting clients at a table"></div>
  <div class="abs hero-shade"></div>
  <h1 class="abs hero-title">NGCHPA</h1>
  <p class="abs hero-sub">HEALTHCARE PRACTICE ADVISORS</p>
  <a class="abs btn hero-btn" href="#">Get Started</a>
  <div class="abs dots"><i></i><i></i><i></i></div>
</section>

<section aria-label="About the society">
  <div class="abs about-frame"></div>
  <div class="abs photo about-photo" role="img" aria-label="Doctor and colleague discussing notes on a tablet"></div>
  <h2 class="abs sec-title" style="left:621px;top:786px">ABOUT THE <em>SOCIETY</em></h2>
  <div class="abs rule" style="left:621px;top:844px"></div>
  <div class="abs tabs" style="left:621px;top:888px;width:468px;height:57px">
    <span class="on">History</span><span>Code Of Ethics</span><span>Leadership</span><span>Committees</span>
  </div>
  <h3 class="abs sub-head" style="left:621px;top:966px">NGCHPA - Our History</h3>
  <div class="abs body-copy" style="left:621px;top:1014px;width:460px">
    <p>The National Guild of Certified Healthcare Practice Advisors (NGCHPA) was founded July 1st, 2006. Its history began when members of the Institute of Certified Practice Advisors, the National Alliance of Clinic Consultants, and the Society of Medical Dental Practice Advisors came together to form one society to best serve practices across all fields.</p>
    <p style="margin-top:22px">The goal of the NGCHPA is the creation of a strong united organization formed from the memberships of the three prior groups.</p>
  </div>
  <a class="abs btn btn-sm" href="#" style="left:621px;top:1268px">Read More</a>
</section>

<section aria-label="Products and services">
  <h2 class="abs sec-title center" style="top:1390px">PRODUCT &amp; <em>SERVICES</em></h2>
  <svg class="abs arrow" style="left:55px;top:1567px" viewBox="0 0 32 32"><circle cx="16" cy="16" r="16" fill="#6a8b2a"/><path d="M19 9l-7 7 7 7" stroke="#fff" stroke-width="3" fill="none"/></svg>
  <svg class="abs arrow" style="left:1109px;top:1567px" viewBox="0 0 32 32"><circle cx="16" cy="16" r="16" fill="#6a8b2a"/><path d="M13 9l7 7-7 7" stroke="#fff" stroke-width="3" fill="none"/></svg>

  <div class="abs card-img" style="left:111px;top:1477px;background:linear-gradient(135deg,#e6e8ee,#7d8fc4 50%,#2f4aa0)" role="img" aria-label="Close-up of Medicare paperwork"></div>
  <h3 class="abs card-title" style="left:111px;top:1718px">Medicare Quarterly Updates Webinars</h3>
  <p class="abs card-text" style="left:111px;top:1783px">Our goal at NGCHPA is to research and interpret the rules, updates and Medicare alerts. We strive to make it easier for providers, clients, and healthcare</p>
  <a class="abs more" href="#" style="left:111px;top:1890px">Read More ...</a>

  <div class="abs card-img" style="left:444px;top:1477px;background:linear-gradient(135deg,#eef1f3,#b9c4cc 55%,#5d7182)" role="img" aria-label="Tablet showing a video call with a doctor"></div>
  <h3 class="abs card-title" style="left:444px;top:1718px">NGCHPA Video Catalog</h3>
  <p class="abs card-text" style="left:444px;top:1762px">2023 Annual Conference Videos<br>2023 Winter Workshop Videos<br>2022 Annual Conference Videos<br>2022 Telehealth Summit Videos<br>2022 Winter Workshop Videos</p>
  <a class="abs more" href="#" style="left:444px;top:1890px">Read More ...</a>

  <div class="abs card-img" style="left:777px;top:1477px;background:linear-gradient(135deg,#c8b89a,#6f6a5e 50%,#2e3338)" role="img" aria-label="Team meeting around an office table"></div>
  <h3 class="abs card-title" style="left:777px;top:1718px">NGCHPA Practice Statistics Report</h3>
  <p class="abs card-text" style="left:777px;top:1783px">Each year the Society surveys its members' clients and compiles a Benchmarks Report on Medical and Dental Income and Expense Averages.</p>
  <a class="abs more" href="#" style="left:777px;top:1890px">Read More ...</a>
</section>

<section aria-label="Foundation">
  <div class="abs band" role="img" aria-label="Green band over a faint photo of a medical team"></div>
  <h2 class="abs band-title center">THE FOUNDATION FOR LEARNING IN<br>PRACTICE ADMINISTRATION</h2>
  <div class="abs rule" style="left:575px;top:2174px;background:#fff"></div>
  <p class="abs band-text">The Foundation for Learning in Practice Administration is a non-profit organization dedicated to improving healthcare delivery through the education of practice management consultants.The Foundation receives funding from individual donors, foundations, government grants, industry publications, healthcare systems, product vendors, healthcare providers and their organizations, practice management consultants and other potential givers.</p>
  <a class="abs btn btn-slate" href="#" style="left:538px;top:2338px;width:124px;height:41px">Read More</a>
</section>

<section aria-label="Our partners">
  <h2 class="abs sec-title center" style="top:2541px"><span>OUR </span><em>PARTNERS</em></h2>
  <div class="abs badge" style="left:111px;top:2637px;width:222px" aria-label="Sponsor badge"><i style="width:190px;height:56px;background:#2b2b2b"></i></div>
  <div class="abs badge" style="left:361px;top:2637px;width:223px" aria-label="Partner badge"><i style="width:130px;height:40px;background:#2c4f86"></i></div>
  <div class="abs badge" style="left:610px;top:2637px;width:224px" aria-label="Partner badge"><i style="width:150px;height:50px;background:#4d6d3e"></i></div>
  <div class="abs badge" style="left:862px;top:2637px;width:223px" aria-label="Partner badge"><i style="width:190px;height:46px;background:#2f9fb0"></i></div>
  <div class="abs badge" style="left:238px;top:2767px;width:222px" aria-label="Partner badge"><i style="width:86px;height:86px;border-radius:50%;background:#7a2c31"></i></div>
  <div class="abs badge" style="left:473px;top:2767px;width:222px" aria-label="Partner badge"><i style="width:204px;height:66px;background:#5c7ee8"></i></div>
  <div class="abs badge" style="left:737px;top:2767px;width:224px" aria-label="Partner badge"><i style="width:150px;height:60px;background:#3a3a3a"></i></div>
</section>

<section aria-label="Upcoming education">
  <h2 class="abs sec-title center" style="top:2941px">UPCOMING <em>EDUCATION</em></h2>
  <svg class="abs arrow" style="left:55px;top:3121px" viewBox="0 0 32 32"><circle cx="16" cy="16" r="16" fill="#6a8b2a"/><path d="M19 9l-7 7 7 7" stroke="#fff" stroke-width="3" fill="none"/></svg>
  <svg class="abs arrow" style="left:1109px;top:3121px" viewBox="0 0 32 32"><circle cx="16" cy="16" r="16" fill="#6a8b2a"/><path d="M13 9l7 7-7 7" stroke="#fff" stroke-width="3" fill="none"/></svg>
  <div class="abs card-img" style="left:111px;top:3031px;height:212px;background:linear-gradient(135deg,#9a8f80,#e9e6e1 50%,#b6b3ae)" role="img" aria-label="Calculator, pen and papers on a desk"></div>
  <div class="abs card-img" style="left:444px;top:3031px;height:212px;background:linear-gradient(135deg,#6d7f8e,#4b5d6d)" role="img" aria-label="Person at a laptop joining a webinar"></div>
  <a class="abs btn" href="#" style="left:548px;top:3118px;width:114px;height:38px">Read More</a>
  <div class="abs card-img" style="left:777px;top:3031px;height:212px;background:linear-gradient(135deg,#ededeb,#cfd0cc 60%,#6f9a86)" role="img" aria-label="Desk calendar pages with dates"></div>
  <h3 class="abs edu-title" style="left:111px;top:3271px">NGCHPA Education Calendar</h3>
  <h3 class="abs edu-title" style="left:444px;top:3271px">NGCHPA Upcoming Webinars</h3>
  <h3 class="abs edu-title" style="left:777px;top:3271px">Quarterly Medicare Updates</h3>
</section>

<section aria-label="About membership">
  <h2 class="abs sec-title" style="left:111px;top:3372px">ABOUT <em>MEMBERSHIP</em></h2>
  <div class="abs rule" style="left:111px;top:3428px"></div>
  <div class="abs tabs" style="left:111px;top:3473px;width:468px;height:56px">
    <span>Areas Of Expertise</span><span class="on" style="padding:0 6px">Become a Member</span><span>Membership FAQ</span>
  </div>
  <h3 class="abs sub-head" style="left:111px;top:3554px;color:var(--green)">Become an NGCHPA Member</h3>
  <p class="abs body-copy" style="left:111px;top:3592px;width:470px">Join us and become a member of the premier Society representing the best in the field of business healthcare consulting! How to join the National Guild of Certified Healthcare Practice Advisors.Society membership consists of individual members, not firms. A candidate for membership is an individual who:</p>
  <ul class="abs bullets" style="left:143px;top:3728px;width:420px">
    <li>Provides business/management consulting professional services to the healthcare industry.</li>
    <li>Conducts themself in a manner reasonably consistent with the Society's Code of Ethics.</li>
  </ul>
  <a class="abs btn btn-sm" href="#" style="left:111px;top:3855px">Read More</a>
  <div class="abs mem-frame"></div>
  <div class="abs mem-photo" role="img" aria-label="Hands joining two puzzle pieces"></div>
</section>

<footer>
  <div class="abs footer"></div>
  <h4 class="abs foot-head" style="left:113px;top:4070px">Quick Link</h4>
  <ul class="abs foot-links" style="left:113px;top:4127px">
    <li>Home</li><li>About the Society</li><li>About Membership</li><li>Products/Services</li><li>Upcoming Education</li>
  </ul>
  <ul class="abs foot-links" style="left:349px;top:4127px">
    <li>Practice Reports</li><li>Foundation(FLPA)</li><li>NGCHPA Sponsors</li><li>Contact Us</li>
  </ul>
  <div class="abs social" style="left:349px;top:4297px"><span>Circl</span><span>Postr</span><span>Linkt</span><span>Vidio</span></div>
  <h4 class="abs foot-head" style="left:624px;top:4070px">Other Links</h4>
  <ul class="abs foot-links" style="left:624px;top:4127px">
    <li>Get Certified(CHPA)</li><li>Find A Consultant</li><li>Current News</li><li>Current Podcasts</li><li>Member Login</li>
  </ul>
  <h4 class="abs foot-head" style="left:921px;top:4070px">Contact Us</h4>
  <div class="abs contact" style="left:921px;top:4125px">
    <p>NGCHPA<br>4820 Linden Park Way<br>#210 Fairview, VA 22031</p>
    <p style="margin-top:18px">Tel: 555-014-2210</p>
    <p style="margin-top:18px">Fax: 555-018-7734</p>
    <p style="margin-top:18px">info@vrtmdp.org</p>
  </div>
  <div class="abs foot-rule"></div>
  <p class="abs legal" style="left:111px">©2024 National Guild of Certified Healthcare Practice Advisors</p>
  <p class="abs legal" style="left:834px;word-spacing:2px">Privacy Policy &nbsp; Site Disclaimer &nbsp; Sitemap</p>
</footer>

</body>
</html>
```